Business Card Design

New business card design

Target Market(s)

Residential & Commercial Property Managers

Industry/Entity Type

Plumbing Services

Contact Information for Business Card

Name - Rowan Keddle, title - Director, Phone Number - 0431 286 517, email - rowan@tbk-plumbing.com.au, Company ABN - 73 215 904 386,

Font styles to use
Sans Serif

Colors
0054AA
0677BA
7BADD7
CADEEF
E8F1F8

```html
<!DOCTYPE html>
<html lang="en">
<head>
<meta charset="utf-8">
<title>TBK Plumbing Services – Business Card</title>
<link rel="stylesheet" href="https://fonts.googleapis.com/css2?family=Lato:wght@400;700&display=swap">
<style>
  :root {
    --blue-deep: #0054AA;
    --blue: #0677BA;
    --blue-mid: #7BADD7;
    --blue-pale: #CADEEF;
    --blue-mist: #E8F1F8;
    --ink: #3a3b3e;
    --charcoal: #2a2b2f;
    --charcoal-dark: #1c1d20;
    --card-light: #f1eff1;
    --card-silver: #d8d5d7;
    --stage: #e4e2e3;
  }
  * { margin: 0; padding: 0; box-sizing: border-box; }
  html, body {
    width: 1200px; height: 734px; overflow: hidden;
    background: var(--stage);
  }
  .card {
    position: absolute; left: 30px; top: 30px;
    width: 1140px; height: 674px;
    border-radius: 34px;
    overflow: hidden;
    background: linear-gradient(100deg, var(--card-silver) 0%, var(--card-light) 35%, #e3e0e2 70%, #d4d1d3 100%);
    font-family: "Lato", sans-serif;
    color: var(--ink);
  }
  .accent-band {
    position: absolute; inset: 0;
    width: 100%; height: 100%;
  }
  .brand {
    position: absolute; left: 79px; top: 86px;
    color: var(--charcoal);
    font-weight: 400;
  }
  .brand-name {
    display: block;
    font-size: 92px; line-height: 1;
    letter-spacing: 4px;
  }
  .brand-tagline {
    display: block;
    margin-top: 38px;
    font-size: 17px;
    letter-spacing: 15px;
    text-transform: lowercase;
  }
  .contact-name {
    position: absolute; left: 79px; top: 300px;
    font-size: 47px; font-weight: 700;
    color: var(--blue);
    text-transform: uppercase;
    letter-spacing: 0.2px;
  }
  .contact-role {
    position: absolute; left: 79px; top: 361px;
    font-size: 28px;
  }
  .contact-list {
    position: absolute; left: 79px; top: 427px;
    list-style: none;
    font-size: 26px;
  }
  .contact-list li {
    display: flex; align-items: center;
    height: 38px;
  }
  .contact-list svg {
    width: 24px; height: 24px;
    margin-right: 20px;
    fill: var(--blue);
  }
  .abn {
    position: absolute; left: 79px; top: 532px;
    font-size: 26px;
  }
  .brand-mark-area {
    position: absolute; left: 652px; top: 22px;
    width: 462px; height: 612px;
    border-radius: 230px 230px 231px 231px;
    background: linear-gradient(160deg, var(--blue) 0%, var(--blue-deep) 70%, var(--blue) 100%);
    box-shadow: 0 0 0 20px var(--card-silver);
  }
</style>
</head>
<body>
  <main class="card">
    <svg class="accent-band" viewBox="0 0 1140 674" aria-hidden="true">
      <defs>
        <linearGradient id="band-shade" x1="0" y1="0" x2="0" y2="1">
          <stop offset="0" stop-color="#3b3c40"/>
          <stop offset="1" stop-color="#1b1c1f"/>
        </linearGradient>
      </defs>
      <path d="M884 0 H1140 V674 H923 C1020 620 1110 520 1110 400 C1110 260 990 120 884 0 Z" fill="url(#band-shade)"/>
    </svg>

    <div class="brand-mark-area" role="img" aria-label="Large brand mark decoration"></div>

    <div class="brand">
      <span class="brand-name">TBK</span>
      <span class="brand-tagline">plumbing services</span>
    </div>

    <h1 class="contact-name">Rowan Keddle</h1>
    <p class="contact-role">Director</p>

    <ul class="contact-list">
      <li>
        <svg viewBox="0 0 24 24" aria-hidden="true"><path d="M6.6 10.8a15.1 15.1 0 0 0 6.6 6.6l2.2-2.2a1 1 0 0 1 1-.25 11.4 11.4 0 0 0 3.6.57 1 1 0 0 1 1 1V20a1 1 0 0 1-1 1A17 17 0 0 1 3 4a1 1 0 0 1 1-1h3.5a1 1 0 0 1 1 1c0 1.25.2 2.45.57 3.57a1 1 0 0 1-.25 1z"/></svg>
        <span>0431 286 517</span>
      </li>
      <li>
        <svg viewBox="0 0 24 24" aria-hidden="true"><path d="M2 5h20v14H2z M4 7v.4l8 5.2 8-5.2V7z" fill-rule="evenodd"/></svg>
        <span>rowan@tbk-plumbing.com.au</span>
      </li>
    </ul>

    <p class="abn">ABN - 73 215 904 386</p>
  </main>
</body>
</html>
```